Salon and Spa Distributor Business Card

Need a business card. We are are distributor in the salon and spa industry. We identify with natural beauty. Need a card with:
Company Name: Petal Quarry"
Title: "President & CEO"
Address
Company Phone number
email
website
Tag Line:" The Professional Salon Source"

Industry/Entity Type

Business

Contact Information for Business Card

Name: Dov Strommen
Title: "President & CEO"
Address: 31 Harlow Ln, Bexmoor, NJ 07813
Company Phone number: 800-463-5918
email: dovstrommen@petalquarry.example
website: www.petalquarry.example

Requirements
Should not have
• No black backgrounds

```html
<!DOCTYPE html>
<html lang="en">
<head>
<meta charset="utf-8">
<title>Petal Quarry – Business Card</title>
<link rel="stylesheet" href="https://fonts.googleapis.com/css2?family=Questrial&display=swap">
<style>
  :root {
    --green-light: #66bb46;
    --green-mid: #3f9a42;
    --green-deep: #086535;
    --white: #ffffff;
    --stage: #eef1ee;
    --card-w: 855px;
    --card-h: 488px;
  }
  * { margin: 0; padding: 0; box-sizing: border-box; }
  html, body {
    width: 1189px;
    height: 1200px;
    overflow: hidden;
    background: var(--stage);
    font-family: "Questrial", sans-serif;
    color: var(--white);
  }
  .card {
    position: absolute;
    left: 167px;
    width: var(--card-w);
    height: var(--card-h);
    border-radius: 22px;
    overflow: hidden;
    background: linear-gradient(180deg, var(--green-light) 0%, var(--green-mid) 55%, var(--green-deep) 100%);
  }
  .card--front { top: 67px; }
  .card--back { top: 625px; }

  .front-brand {
    position: absolute;
    left: 0; right: 0;
    top: 205px;
    text-align: center;
  }
  .brand-name {
    font-size: 50px;
    line-height: 1;
    letter-spacing: 0.5px;
  }
  .brand-tagline {
    font-size: 21px;
    letter-spacing: 2px;
    margin-top: 8px;
  }

  .back-info {
    position: absolute;
    left: 51px;
    top: 30px;
  }
  .person {
    margin-top: 78px;
  }
  .person-name { font-size: 29px; line-height: 1.1; }
  .person-title { font-size: 22px; margin-top: 2px; }
  .address {
    margin-top: 40px;
    font-size: 22px;
    line-height: 29px;
    font-style: normal;
  }
  .contacts {
    list-style: none;
    margin-top: 14px;
    font-size: 22px;
  }
  .contacts li {
    display: flex;
    align-items: center;
    gap: 10px;
    height: 28px;
  }
  .contact-icon {
    width: 24px;
    height: 22px;
    flex: none;
  }
  .back-art {
    position: absolute;
    right: 0;
    top: 0;
    width: 100%;
    height: 100%;
    pointer-events: none;
  }
</style>
</head>
<body>

<section class="card card--front" aria-label="Card front">
  <div class="front-brand">
    <div class="brand-name">Petal Quarry</div>
    <div class="brand-tagline">The Professional Salon Source</div>
  </div>
</section>

<section class="card card--back" aria-label="Card back">
  <svg class="back-art" viewBox="0 0 855 488" role="img" aria-label="Illustration of a woman's profile with flowing leafy green hair">
    <defs>
      <linearGradient id="artTone" x1="0" y1="0" x2="1" y2="1">
        <stop offset="0" stop-color="#ffffff"/>
        <stop offset="0.45" stop-color="#e6f3df"/>
        <stop offset="0.75" stop-color="#9fd386"/>
        <stop offset="1" stop-color="#ffffff"/>
      </linearGradient>
    </defs>
    <path d="M560 0 C470 120 500 300 430 488 L855 488 L855 0 Z" fill="url(#artTone)"/>
  </svg>

  <div class="back-info">
    <div class="brand-name">Petal Quarry</div>
    <div class="brand-tagline">The Professional Salon Source</div>

    <div class="person">
      <div class="person-name">Dov Strommen</div>
      <div class="person-title">President &amp; CEO</div>
    </div>

    <address class="address">
      31 Harlow Ln,<br>
      Bexmoor, NJ 07813
    </address>

    <ul class="contacts">
      <li>
        <svg class="contact-icon" viewBox="0 0 24 22" aria-hidden="true">
          <rect width="24" height="22" fill="#fff"/>
          <path d="M5 9c0-3 14-3 14 0v2h-3V9H8v2H5z" fill="#086535"/>
          <rect x="7" y="11" width="10" height="7" rx="1" fill="#086535"/>
        </svg>
        800-463-5918
      </li>
      <li>
        <svg class="contact-icon" viewBox="0 0 24 22" aria-hidden="true">
          <rect width="24" height="22" fill="#fff"/>
          <rect x="4" y="5" width="16" height="12" fill="none" stroke="#086535" stroke-width="1.6"/>
          <path d="M4 5l8 7 8-7M4 17l6-6M20 17l-6-6" fill="none" stroke="#086535" stroke-width="1.6"/>
        </svg>
        dovstrommen@petalquarry.example
      </li>
      <li>
        <svg class="contact-icon" viewBox="0 0 24 22" aria-hidden="true">
          <rect width="24" height="22" fill="#fff"/>
          <circle cx="12" cy="11" r="7" fill="none" stroke="#086535" stroke-width="1.5"/>
          <ellipse cx="12" cy="11" rx="3" ry="7" fill="none" stroke="#086535" stroke-width="1.2"/>
          <path d="M5 11h14M6 7.5h12M6 14.5h12" stroke="#086535" stroke-width="1.2"/>
        </svg>
        www.petalquarry.example
      </li>
    </ul>
  </div>
</section>

</body>
</html>
```